Body Wash & Shampoo Label Design

Hello everyone,

I need a new logo/label design for a sister line of products to our main line. The Brand name is Velmora Trailside.

Here’s some insight to provide some inspiration. This brand will be social media based and will focus on adventure, travel, hiking, camping, and all other outdoors activities. Target market is outdoorsman – women. We will also be allocating a percentage of sales to various conservation efforts which we are narrowing down as we speak.

I’m not exactly sure what we are looking for in a logo/label designs so we are open to ideas and promote creativity. That said, we are looking for a simple and clean design that also speaks to our target market and would like the logo & label to be done at the same time so they compliment each other and fit well together.

Please incorporate an accent color somewhere in the design so new fragrances can be added down the line. This label will be going on a 16 fl oz cylindrical bottle with a toggle cap.

Label Details:

Width: 7.4 in
Height: 5.5 in
Distance from center of front to center of back: 3.7 in

Front (left):
- Logo
- Product Name: Driftwell Shampoo & Body Cleanser
- Highlights:
o No Rinse Nourishing Formula
o Sooths & Conditions
o Non-Sensitizing
o Non-Allergenic
- 16 Fl. Oz.

Back (right):

Tagline: More Cleanse, Less Hassle

Directions: Moisten wash cloth with Driftwell Shampoo & body cleanser. Use wash cloth to gently cleanse desired area. Pat dry if necessary. When shampooing, use was cloth to gently massage hair and scalp. Let air dry.

Warning: For external use only. Rinse eyes with water if contact should occur. Discontinue use in the case of local irritation. Contact physician if irritation persists for extended period of time.

Ingredients: Water, Disodium Cocoamphodiactate, Sodium C14-16 Olefine Sulfonate, ppg-2 hydroxyethyl Cocamide, Styrene/Acrylates Copolymer, Solvarin IV, Acrylates/C10-30 Alkyl Acrylate Crosspolymer, Fragrance, Aloe Barbadeniss Leaf Juice

Made in USA (either logo or words)

Address:
Quillan Products
214 Ashcombe Ln
Dover, NJ 07899

Barcode is also attached below. Looking forward to seeing your designs and thanks for the help! Let me know if you have any questions.

- Merle

Target Market(s)

Outdoorsman/women

Logo Text

Velmora Trailside

Colors

Designer to choose colors to be used in the design.

```html
<!DOCTYPE html>
<html lang="en">
<head>
<meta charset="utf-8">
<title>Velmora Trailside – Driftwell Shampoo &amp; Body Cleanser Label</title>
<link rel="stylesheet" href="https://fonts.googleapis.com/css2?family=Oswald:wght@300;400;500&family=Montserrat:wght@400;500;700&display=swap">
<style>
  :root {
    --page: #ffffff;
    --panel: #000000;
    --ink: #ffffff;
    --accent: #f0901e;
  }
  * { margin: 0; padding: 0; box-sizing: border-box; }
  html, body { width: 1200px; height: 1000px; overflow: hidden; background: var(--page); }
  .canvas { position: relative; width: 1200px; height: 1000px; }
  .label-panel {
    position: absolute; top: 228px; width: 532px; height: 532px;
    background: var(--panel); color: var(--ink);
  }
  .label-front { left: 39px; }
  .label-back { left: 613px; }

  .brand-lockup {
    position: absolute; display: flex; flex-direction: column; align-items: center;
    font-family: 'Oswald', sans-serif; font-weight: 400; color: var(--ink);
    text-transform: uppercase; line-height: 1;
  }
  .brand-dot { border-radius: 50%; background: var(--accent); }
  .front-brand { left: 0; width: 532px; top: 42px; }
  .front-brand .brand-dot { width: 44px; height: 44px; margin-bottom: 14px; }
  .front-brand .brand-name { font-size: 58px; letter-spacing: 1px; text-align: center; }
  .front-brand .brand-name span { display: block; }
  .front-brand .brand-name span + span { font-size: 30px; letter-spacing: 7px; margin-top: 8px; }

  .product-name {
    position: absolute; top: 245px; left: 0; width: 532px; text-align: center;
    font-family: 'Oswald', sans-serif; font-weight: 300; font-size: 38px;
    line-height: 48px; text-transform: uppercase;
  }
  .highlights {
    position: absolute; top: 372px; left: 0; width: 532px; list-style: none; text-align: center;
    font-family: 'Montserrat', sans-serif; font-weight: 500; font-size: 12.5px; line-height: 15.5px;
    text-transform: uppercase;
  }
  .highlights li::before { content: "• "; }
  .net-volume {
    position: absolute; top: 474px; left: 0; width: 532px; text-align: center;
    font-family: 'Montserrat', sans-serif; font-weight: 500; font-size: 17px; color: var(--accent);
  }
  .net-volume .estimated { font-weight: 700; font-size: 24px; margin: 0 4px; }

  .back-brand { left: 42px; top: 36px; width: 146px; }
  .back-brand .brand-dot { width: 26px; height: 26px; margin-bottom: 8px; }
  .back-brand .brand-name { font-size: 30px; text-align: center; }
  .back-brand .brand-name span { display: block; }
  .back-brand .brand-name span + span { font-size: 16px; letter-spacing: 3px; margin-top: 4px; }

  .tagline {
    position: absolute; left: 250px; top: 58px; width: 210px; text-align: center;
    font-family: 'Oswald', sans-serif; font-weight: 500; font-size: 24px; line-height: 29px;
    text-transform: uppercase;
  }
  .info-block {
    position: absolute; left: 42px; width: 449px;
    font-family: 'Montserrat', sans-serif; font-size: 12.3px; line-height: 15.5px; text-align: justify;
  }
  .info-block h3 { font-size: 12.3px; font-weight: 700; }
  .directions { top: 145px; }
  .warning { top: 237px; }
  .ingredients { top: 315px; }

  .made-in-usa {
    position: absolute; left: 230px; top: 456px; display: flex; align-items: center; gap: 4px;
    font-family: 'Oswald', sans-serif; font-weight: 500; line-height: 1;
  }
  .made-in-usa .flag-mark { display: flex; flex-direction: column; gap: 2px; }
  .made-in-usa .stars { font-size: 10px; letter-spacing: 1px; }
  .made-in-usa .stripe { width: 37px; height: 3px; background: var(--ink); }
  .made-in-usa .words { display: flex; flex-direction: column; }
  .made-in-usa .small { font-size: 12px; }
  .made-in-usa .big { font-size: 27px; }

  .address {
    position: absolute; left: 355px; top: 442px; width: 136px; text-align: center; font-style: normal;
    font-family: 'Montserrat', sans-serif; font-weight: 500; font-size: 14px; line-height: 14px;
  }
  .address strong { display: block; font-weight: 700; }
</style>
</head>
<body>
<main class="canvas">
  <section class="label-panel label-front">
    <div class="brand-lockup front-brand">
      <div class="brand-dot"></div>
      <div class="brand-name"><span>Velmora</span><span>Trailside</span></div>
    </div>
    <h1 class="product-name">Driftwell Shampoo<br>&amp; Body Cleanser</h1>
    <ul class="highlights">
      <li>No Rinse Nourishing Formula</li>
      <li>Sooths &amp; Conditions</li>
      <li>Non-Sensitizing</li>
      <li>Non-Allergenic</li>
    </ul>
    <p class="net-volume">354ML<span class="estimated">℮</span>12 FL OZ</p>
  </section>

  <section class="label-panel label-back">
    <div class="brand-lockup back-brand">
      <div class="brand-dot"></div>
      <div class="brand-name"><span>Velmora</span><span>Trailside</span></div>
    </div>
    <h2 class="tagline">More Cleanse,<br>Less Hassle</h2>

    <div class="info-block directions">
      <h3>Directions:</h3>
      <p>Moisten wash cloth with Driftwell Shampoo &amp; body cleanser. Use wash cloth to gently cleanse desired area. Pat dry if necessary. When shampooing, use was cloth to gently massage hair and scalp. Let air dry.</p>
    </div>
    <div class="info-block warning">
      <h3>Warning:</h3>
      <p>For external use only. Rinse eyes with water if contact should occur. Discontinue use in the case of local irritation. Contact physician if irritation persists for extended period of time.</p>
    </div>
    <div class="info-block ingredients">
      <h3>Ingredients:</h3>
      <p>Water, Disodium Cocoamphodiactate, Sodium C14-16 Olefine Sulfonate, ppg-2 hydroxyethyl Cocamide, Styrene/Acrylates Copolymer, Solvarin IV, Acrylates/C10-30 Alkyl Acrylate Crosspolymer, Fragrance, Aloe Barbadeniss Leaf Juice.</p>
    </div>

    <div class="made-in-usa">
      <div class="flag-mark">
        <span class="stars">★★★</span>
        <span class="stripe"></span>
        <span class="stripe"></span>
        <span class="stripe"></span>
      </div>
      <div class="words"><span class="small">MADE IN</span><span class="big">USA</span></div>
    </div>

    <address class="address">
      <strong>Address:</strong>
      Quillan Products<br>
      214 Ashcombe Ln<br>
      Dover, NJ 07899
    </address>
  </section>
</main>
</body>
</html>
```